Walk Beside The River

Business Card design

Target Market(s)

People who require support in the commnity

Industry/Entity Type

Mental Health Support

Contact Information for Business Card

Mental Health Support Rosalind Tavener walkbesidetheriver@mailcove.com.au 0481 637 092 PO Box 926 Kestrelford QLD 4587

Colors
6B429C
8869AF
B7A5CE
E3DAEB
F3F0F8

Requirements
Must have
• Logo & details listed above
Should not have
• No red or orange

```html
<!DOCTYPE html>
<html lang="en">
<head>
<meta charset="utf-8">
<title>Walk Beside The River – Business Card</title>
<link href="https://fonts.googleapis.com/css2?family=Open+Sans:wght@400;600&display=swap" rel="stylesheet">
<style>
  :root {
    --stage: #2b2a30;
    --card-dark: #1f1e24;
    --card-light: #ffffff;
    --sun-yellow: #f0e833;
    --brand-purple: #6b429c;
    --text-ink: #1a1a1a;
  }
  html, body {
    margin: 0;
    width: 1200px;
    height: 780px;
    overflow: hidden;
    background: var(--stage);
    font-family: "Open Sans", sans-serif;
  }
  .stage {
    position: relative;
    width: 1200px;
    height: 780px;
  }
  .card {
    position: absolute;
    top: 238px;
    width: 530px;
    height: 303px;
    border-radius: 22px;
    overflow: hidden;
    box-shadow: 0 0 0 3px var(--sun-yellow), 0 18px 40px rgba(0,0,0,.45);
  }
  .card--back {
    left: 46px;
    background: var(--card-dark);
  }
  .card--front {
    left: 624px;
    background: var(--card-light);
  }
  .card__decor {
    position: absolute;
    inset: 0;
  }
  .brand {
    position: absolute;
    left: 34px;
    top: 46px;
    display: flex;
    align-items: center;
    gap: 14px;
  }
  .brand__dot {
    width: 58px;
    height: 58px;
    border-radius: 50%;
    background: var(--brand-purple);
  }
  .brand__name {
    font-weight: 600;
    font-size: 19px;
    color: var(--brand-purple);
    letter-spacing: .5px;
  }
  .details {
    position: absolute;
    left: 34px;
    top: 138px;
    color: var(--text-ink);
    font-size: 13.5px;
    line-height: 19px;
  }
  .details__role, .details__name { margin: 0; }
  .details__role { font-weight: 600; }
  .contact {
    list-style: none;
    margin: 6px 0 0;
    padding: 0;
  }
  .contact__item {
    display: flex;
    align-items: center;
    gap: 8px;
  }
  .contact__icon {
    width: 13px;
    height: 13px;
    fill: var(--brand-purple);
    flex: none;
  }
</style>
</head>
<body>
<main class="stage">

  <section class="card card--back" aria-label="Card back"></section>

  <section class="card card--front" aria-label="Card front">
    <svg class="card__decor" viewBox="0 0 530 303" aria-hidden="true">
      <path d="M390 0 H530 V160 C500 110 450 55 390 0 Z" fill="var(--sun-yellow)"/>
      <path d="M530 164 V186 L350 254 C336 258 322 258 314 256 C330 250 340 244 352 236 Z" fill="var(--brand-purple)"/>
      <path d="M0 280 H310 C326 276 340 268 350 262 L366 258 C350 276 326 292 306 303 H0 Z" fill="var(--sun-yellow)"/>
    </svg>

    <div class="brand">
      <span class="brand__dot"></span>
      <span class="brand__name">Walk Beside The River</span>
    </div>

    <div class="details">
      <p class="details__role">Mental Health Support</p>
      <p class="details__name">Rosalind Tavener</p>
      <ul class="contact">
        <li class="contact__item">
          <svg class="contact__icon" viewBox="0 0 24 24"><path d="M6.6 10.8a15 15 0 0 0 6.6 6.6l2.2-2.2a1 1 0 0 1 1-.25 11.4 11.4 0 0 0 3.6.57 1 1 0 0 1 1 1V20a1 1 0 0 1-1 1A17 17 0 0 1 3 4a1 1 0 0 1 1-1h3.5a1 1 0 0 1 1 1c0 1.25.2 2.45.57 3.57a1 1 0 0 1-.25 1z"/></svg>
          <span>0481 637 092</span>
        </li>
        <li class="contact__item">
          <svg class="contact__icon" viewBox="0 0 24 24"><path d="M2 5h20v14H2zm2 2v.5l8 5 8-5V7zm0 2.9V17h16V9.9l-8 5z"/></svg>
          <span>walkbesidetheriver@mailcove.com.au</span>
        </li>
        <li class="contact__item">
          <svg class="contact__icon" viewBox="0 0 24 24"><path d="M12 2a7 7 0 0 0-7 7c0 5 7 13 7 13s7-8 7-13a7 7 0 0 0-7-7zm0 9.5A2.5 2.5 0 1 1 12 6.5a2.5 2.5 0 0 1 0 5z"/></svg>
          <span>PO Box 926 Kestrelford QLD 4587</span>
        </li>
      </ul>
    </div>
  </section>

</main>
</body>
</html>
```